Business Card Design Project

I need a business card design for my law office. I already have a logo.

I am an employment attorney who represents clients who have been wrongfully terminated or have been discriminated against by their employer.

I would like a unique, clean design using the colors in the logo or colors that complement the logo.

Target Market(s)

Clients, potential clients, other attorneys and others.

Industry/Entity Type

Attorney

Requirements
Must have
• I would like to use both sides of the card.

The information on the card must be easy to read.

Here is my information:

T. Dale Ostrovin
3857 E. Harbel Blvd., Suite 204
Fresno, California 93814
559-618-3074
559-782-4531 fax
dale@lawtdo-example.com
Nice to have
• QR Code? I would like to see designs incorporating a nice-looking QR code. Look at this example:

Notice the second QR code in the article - the color.

```html
<!DOCTYPE html>
<html lang="en">
<head>
<meta charset="utf-8">
<title>T. Dale Ostrovin Law Office – Business Card</title>
<link rel="stylesheet" href="https://fonts.googleapis.com/css2?family=Tinos:wght@400&display=swap">
<style>
  :root {
    --backdrop: #b3bba3;
    --card-white: #ffffff;
    --card-blue: #0048ff;
    --accent-cyan: #27b4e6;
    --mark-blue: #1f6fff;
    --ink: #111111;
    --shadow: rgba(40, 48, 30, 0.35);
  }
  * { box-sizing: border-box; margin: 0; padding: 0; }
  html, body {
    width: 1200px;
    height: 900px;
    overflow: hidden;
    background: var(--backdrop);
    font-family: "Tinos", "Times New Roman", serif;
  }
  .canvas {
    position: relative;
    width: 1200px;
    height: 900px;
  }
  .card {
    position: absolute;
    top: 307px;
    width: 500px;
    height: 286px;
    border-radius: 30px;
    box-shadow: 0 6px 14px var(--shadow);
  }
  .card--front {
    left: 70px;
    background: var(--card-white);
    color: var(--ink);
  }
  .card--back {
    left: 630px;
    background: var(--card-blue);
    display: flex;
    align-items: center;
    justify-content: center;
  }

  .brand {
    display: flex;
    align-items: center;
    gap: 10px;
    color: var(--accent-cyan);
    white-space: nowrap;
  }
  .brand__square {
    width: 26px;
    height: 26px;
    background: var(--mark-blue);
  }
  .brand__name { font-size: 21px; }

  .card--front .brand {
    position: absolute;
    top: 38px;
    left: 0;
    right: 0;
    justify-content: center;
  }

  .card--back .brand { color: var(--card-white); gap: 16px; }
  .card--back .brand__square { width: 40px; height: 40px; background: var(--card-white); }
  .card--back .brand__name { font-size: 31px; }

  .holder-name {
    position: absolute;
    top: 112px;
    left: 0;
    right: 0;
    text-align: center;
    font-size: 17px;
    color: var(--accent-cyan);
  }
  .contact {
    position: absolute;
    top: 172px;
    font-size: 15.5px;
    line-height: 21px;
  }
  .contact--address { left: 46px; }
  .contact--phones { right: 36px; text-align: right; }
  .email {
    position: absolute;
    top: 232px;
    left: 0;
    right: 0;
    text-align: center;
    font-size: 15.5px;
  }
</style>
</head>
<body>
<main class="canvas">
  <section class="card card--front" aria-label="Business card front">
    <div class="brand">
      <span class="brand__square" aria-hidden="true"></span>
      <span class="brand__name">T. Dale Ostrovin Law Office</span>
    </div>
    <p class="holder-name">T. Dale Ostrovin</p>
    <address class="contact contact--address" style="font-style:normal">
      3857 E. Harbel Blvd., Suite 204<br>
      Fresno, California 93814
    </address>
    <p class="contact contact--phones">
      tel: 559 618 3074<br>
      fax: 559 782 4531
    </p>
    <p class="email">dale@lawtdo-example.com</p>
  </section>

  <section class="card card--back" aria-label="Business card back">
    <div class="brand">
      <span class="brand__square" aria-hidden="true"></span>
      <span class="brand__name">T. Dale Ostrovin Law Office</span>
    </div>
  </section>
</main>
</body>
</html>
```